Automotive Accessories Business Card

Design a business template that match our new logo design and our industry.

https://www.qelmotorgear.com/

Target Market(s)

Aftermarket auto parts and accessories

Industry/Entity Type

automotive

Contact Information for Business Card

company logo

Font styles to use
Serif
Sans Serif

Colors
EB3D1F
EC4F4E
F09395
F8D3D4
FCEDEE

```html
<!DOCTYPE html>
<html lang="en">
<head>
<meta charset="utf-8">
<title>QEL Motor Gear – Business Card</title>
<link rel="stylesheet" href="https://fonts.googleapis.com/css2?family=Poppins:wght@400;500;700;800&display=swap">
<style>
  :root {
    --red: #d71f26;
    --red-dark: #c21b22;
    --ink: #3a3a3c;
    --paper: #ffffff;
    --band: #e6e6e6;
    --stage: #2e2e2e;
  }
  * { box-sizing: border-box; margin: 0; padding: 0; }
  html, body { width: 1200px; height: 866px; overflow: hidden; }
  body {
    background: var(--stage);
    font-family: "Poppins", sans-serif;
    position: relative;
  }
  .card {
    position: absolute;
    left: 320px;
    width: 560px;
    height: 320px;
    overflow: hidden;
    box-shadow: 0 10px 24px rgba(0,0,0,.45);
  }
  .card-front { top: 90px; background: var(--red); }
  .card-back { top: 456px; background: var(--paper); }
  .card-art { position: absolute; inset: 0; width: 100%; height: 100%; }

  .wordmark {
    position: absolute;
    font-weight: 800;
    letter-spacing: 2px;
    white-space: nowrap;
    display: flex;
    align-items: center;
    gap: 12px;
  }
  .wordmark .mark-square { width: 18px; height: 18px; display: block; }
  .card-front .wordmark {
    color: var(--paper);
    font-size: 42px;
    left: 0; right: 0; top: 128px;
    justify-content: center;
  }
  .card-front .mark-square { background: var(--paper); }
  .card-back .wordmark {
    color: var(--ink);
    font-size: 26px;
    left: 34px; top: 30px;
  }
  .card-back .mark-square { background: var(--red); width: 14px; height: 14px; }

  .holder { position: absolute; left: 34px; top: 84px; }
  .holder-name { color: var(--red); font-weight: 800; font-size: 21px; letter-spacing: 1px; text-transform: uppercase; }
  .holder-role { color: #222; font-size: 13px; margin-top: -2px; }
  .rule { position: absolute; height: 1px; background: #222; }
  .rule-top { left: 34px; top: 136px; width: 300px; }
  .rule-bottom { right: 30px; top: 214px; width: 250px; }

  .contacts { position: absolute; left: 34px; top: 146px; list-style: none; font-size: 13px; color: #222; }
  .contacts li { display: flex; align-items: center; gap: 8px; line-height: 22px; }
  .contacts svg { width: 12px; height: 12px; fill: var(--red); }

  .address { position: absolute; right: 30px; top: 222px; font-size: 12.5px; color: #222; text-align: right; line-height: 17px; }
  .website { position: absolute; right: 30px; bottom: 9px; font-size: 13px; color: var(--paper); letter-spacing: .5px; }
</style>
</head>
<body>

<section class="card card-front" aria-label="Card front">
  <svg class="card-art" viewBox="0 0 560 320" aria-hidden="true">
    <polygon points="260,320 560,170 560,320" fill="var(--red-dark)"/>
    <polygon points="0,260 560,60 560,110 0,320" fill="var(--red-dark)" opacity=".5"/>
  </svg>
  <div class="wordmark"><span class="mark-square"></span>QEL MOTOR GEAR</div>
</section>

<section class="card card-back" aria-label="Card back">
  <svg class="card-art" viewBox="0 0 560 320" aria-hidden="true">
    <polygon points="300,230 560,110 560,180 360,250" fill="var(--band)"/>
    <polygon points="380,300 560,210 560,290 470,320 380,320" fill="var(--band)"/>
    <path d="M0,240 L180,302 L560,302 L560,320 L0,320 Z" fill="var(--red)"/>
    <path d="M0,232 L200,298 L0,298 Z" fill="var(--ink)" opacity=".0"/>
    <path d="M0,236 L170,296 L0,296 Z" fill="var(--ink)"/>
    <path d="M0,246 L160,302 L0,302 Z" fill="var(--paper)"/>
    <path d="M0,252 L180,316 L0,320 Z" fill="var(--red)"/>
    <path d="M200,300 Q215,286 240,286 L560,286 L560,320 L180,320 Z" fill="var(--red)"/>
  </svg>

  <div class="wordmark"><span class="mark-square"></span>QEL MOTOR GEAR</div>

  <div class="holder">
    <p class="holder-name">Daniel Reyes</p>
    <p class="holder-role">Managing Director</p>
  </div>
  <div class="rule rule-top"></div>

  <ul class="contacts">
    <li><svg viewBox="0 0 24 24"><path d="M6.6 10.8a15 15 0 0 0 6.6 6.6l2.2-2.2c.3-.3.7-.4 1-.2 1.1.4 2.3.6 3.6.6.6 0 1 .4 1 1V20c0 .6-.4 1-1 1A17 17 0 0 1 3 4c0-.6.4-1 1-1h3.5c.6 0 1 .4 1 1 0 1.3.2 2.5.6 3.6.1.3 0 .7-.2 1z"/></svg>044-210 387 654</li>
    <li><svg viewBox="0 0 24 24"><path d="M2 5h20v14H2z M2 5l10 8 10-8" stroke="#fff" stroke-width="1.5"/></svg>info@qelmotorgear.com</li>
  </ul>

  <div class="rule rule-bottom"></div>
  <p class="address">88, Torque Avenue, Suite 4<br>30817, Westland</p>
  <p class="website">www.qelmotorgear.com</p>
</section>

</body>
</html>
```